Detail Shop Business card design

i need a business card design for my new detailing company called 'Brisk's Polish Works'. i want an all black and white design . simple, direct and to the point. i want the designer to choose a fitting font to match the logothe front should have logo, address, phone and email and the back side should have a slogan and text indicating that we offer services on anything including cars, trucks, motorcycles and RVs. slogan will read "we take pride in your ride"
maybe also very small on the back side the IG icon with Brisks_Polish_Works

phone 208.417.6352
address 3847 E Larkin Ave
Spokane WA 99214
email: BrisksPolish@mailvexo.com

Target Market(s)

all ages , auto enthusiasts

Industry/Entity Type

Automotive

Contact Information for Business Card

the front should have logo, address, phone and email and the back side should have a slogan and text indicating that we offer services on anything including cars, trucks, motorcycles and RVs. slogan will read "we take pride in your ride"

phone 208.417.6352
address 3847 E Larkin Ave
Spokane WA 99214

Colors
000000
ffffff

Requirements
Must have
• bold font and very simple design with good spacing
Nice to have
• anything creative from the designer indicating we service any types of vehicles
Should not have
• any colors ,

```html
<!DOCTYPE html>
<html lang="en">
<head>
<meta charset="utf-8">
<title>Brisk's Polish Works – Business Card</title>
<link rel="stylesheet" href="https://fonts.googleapis.com/css2?family=Roboto+Slab:wght@400;700&display=swap">
<style>
  :root {
    --ink: #000000;
    --card-dark: #0a0a0a;
    --paper: #ffffff;
    --stage: #e9e9e9;
    --rule: #2a2a2a;
    --muted: #3a3a3a;
  }
  * { margin: 0; padding: 0; box-sizing: border-box; }
  html, body {
    width: 1200px; height: 912px; overflow: hidden;
    background: var(--stage);
    font-family: "Roboto Slab", Georgia, serif;
  }
  .stage { position: relative; width: 1200px; height: 912px; }

  .card {
    position: absolute;
    width: 580px; height: 330px;
    border-radius: 18px;
    box-shadow: 0 6px 18px rgba(0,0,0,.18);
    overflow: hidden;
  }

  /* Back side */
  .card--back {
    left: 70px; top: 60px;
    background: var(--card-dark);
    color: var(--paper);
    display: flex; flex-direction: column; align-items: center; justify-content: center;
  }
  .brand {
    display: flex; align-items: center; gap: 12px;
    font-weight: 700; font-size: 30px; letter-spacing: .5px;
  }
  .brand__dot {
    width: 22px; height: 22px; border-radius: 50%;
    background: currentColor; flex: none;
  }
  .card--back .brand { margin-bottom: 46px; }
  .slogan {
    display: flex; align-items: center; gap: 12px;
    font-size: 17px; letter-spacing: 1.5px; text-transform: uppercase;
  }
  .slogan::before, .slogan::after {
    content: ""; width: 50px; height: 1px; background: var(--paper);
  }
  .services {
    margin-top: 14px;
    font-size: 20px; letter-spacing: 1px; text-transform: uppercase;
  }

  /* Front side */
  .card--front {
    left: 560px; top: 520px;
    background: var(--paper);
    color: var(--ink);
  }
  .card--front .brand {
    position: absolute; left: 34px; top: 128px;
    font-size: 22px; color: var(--ink);
  }
  .card--front .brand__dot { width: 18px; height: 18px; }
  .person {
    position: absolute; right: 34px; top: 30px; text-align: right;
  }
  .person__name { font-size: 24px; font-weight: 700; letter-spacing: 1px; text-transform: uppercase; }
  .person__role { font-size: 13px; color: var(--muted); }
  .rule { position: absolute; height: 1px; background: var(--rule); }
  .rule--top { left: 290px; right: 30px; top: 98px; }
  .rule--bottom { left: 30px; right: 260px; top: 232px; }
  .address {
    position: absolute; right: 34px; top: 118px; text-align: right;
    font-size: 15px; line-height: 1.55;
  }
  .contacts {
    position: absolute; left: 34px; top: 246px; list-style: none;
    font-size: 16px; line-height: 1.5;
  }
  .contacts li { display: flex; align-items: center; gap: 10px; }
  .contacts svg { width: 13px; height: 13px; flex: none; }
</style>
</head>
<body>
<main class="stage">

  <section class="card card--back" aria-label="Card back">
    <div class="brand"><span class="brand__dot"></span>Brisk's Polish Works</div>
    <p class="slogan">We take pride in your ride</p>
    <p class="services">Cars - Trucks - Motorcycles and RVs</p>
  </section>

  <section class="card card--front" aria-label="Card front">
    <div class="person">
      <div class="person__name">Dorian Hale</div>
      <div class="person__role">Director</div>
    </div>
    <div class="rule rule--top"></div>
    <div class="brand"><span class="brand__dot"></span>Brisk's Polish Works</div>
    <address class="address" style="font-style:normal">
      3847 E Larkin Ave<br>Spokane WA 99214
    </address>
    <div class="rule rule--bottom"></div>
    <ul class="contacts">
      <li>
        <svg viewBox="0 0 16 16" aria-hidden="true"><path d="M3 1l3 3-2 2c1 2 3 4 5 5l2-2 3 3-2 2C7 14 2 9 1 3z" fill="#000"/></svg>
        208.417.6352
      </li>
      <li>
        <svg viewBox="0 0 16 16" aria-hidden="true"><rect x="1.5" y="3.5" width="13" height="9" fill="none" stroke="#000" stroke-width="1.4"/><path d="M1.5 3.5l6.5 5 6.5-5" fill="none" stroke="#000" stroke-width="1.4"/></svg>
        BrisksPolish@mailvexo.com
      </li>
      <li>
        <svg viewBox="0 0 16 16" aria-hidden="true"><circle cx="8" cy="8" r="6.5" fill="none" stroke="#000" stroke-width="1.4"/><path d="M1.5 8h13M8 1.5c-3 3-3 10 0 13M8 1.5c3 3 3 10 0 13" fill="none" stroke="#000" stroke-width="1.1"/></svg>
        www.BrisksPolish.com
      </li>
    </ul>
  </section>

</main>
</body>
</html>
```